Bright Harbor Painters Banner

Create a banner that displays and reinforces Bright Harbor Painters’ brand identity while promoting our interior painting services. The banner will be displayed at indoor venues through the winter. The design should be clean, professional, and visually recognizable to both new and returning customers. See attached design brief & logo source files.

```html
<!DOCTYPE html>
<html lang="en">
<head>
<meta charset="utf-8">
<title>Bright Harbor Painters Banner</title>
<link rel="stylesheet" href="https://fonts.googleapis.com/css2?family=Lexend:wght@400;500;600;700&display=swap">
<style>
  :root {
    --page: #e9e6df;
    --brand-green: #234d33;
    --brand-green-deep: #1c4029;
    --ink-green: #1f4a35;
    --cream: #f4ecd8;
    --cream-text: #f1e9d6;
    --ink: #1e2a22;
    --accent-orange: #c8501e;
    --brush-orange: #e06b26;
  }
  * { box-sizing: border-box; margin: 0; padding: 0; }
  html, body {
    width: 1200px;
    height: 1200px;
    overflow: hidden;
    background: var(--page);
  }
  body {
    display: flex;
    align-items: center;
    justify-content: center;
    font-family: "Lexend", sans-serif;
  }
  .banner {
    width: 1120px;
    height: 460px;
    display: flex;
    background: var(--cream);
    box-shadow: 0 10px 30px rgba(0,0,0,0.12);
  }
  .brand-panel {
    width: 360px;
    background: linear-gradient(160deg, var(--brand-green), var(--brand-green-deep));
    display: flex;
    flex-direction: column;
    align-items: center;
    justify-content: center;
    text-align: center;
    color: var(--cream-text);
    padding: 30px;
  }
  .brand-name {
    font-weight: 600;
    font-size: 52px;
    line-height: 1.02;
    letter-spacing: 0.5px;
    text-transform: uppercase;
  }
  .brand-tagline {
    margin-top: 18px;
    font-weight: 400;
    font-size: 18px;
    line-height: 1.35;
  }
  .offer-panel {
    flex: 1;
    position: relative;
    padding: 44px 40px 40px 42px;
    color: var(--ink);
  }
  .headline {
    font-weight: 700;
    font-size: 60px;
    line-height: 1.05;
    color: var(--ink-green);
    text-transform: uppercase;
    letter-spacing: 0.5px;
  }
  .services {
    margin-top: 26px;
    font-weight: 500;
    font-size: 28px;
    line-height: 1.35;
  }
  .cta {
    margin-top: 26px;
    font-weight: 500;
    font-size: 28px;
  }
  .cta-url {
    font-weight: 600;
    font-size: 34px;
    color: var(--accent-orange);
  }
  .brush-art {
    position: absolute;
    right: 44px;
    top: 130px;
    width: 120px;
    height: 200px;
    background: linear-gradient(200deg, var(--brush-orange), #c9571b);
    border-radius: 14px 14px 6px 6px;
    opacity: 0.9;
  }
</style>
</head>
<body>
  <main class="banner">
    <section class="brand-panel">
      <h1 class="brand-name">Bright<br>Harbor<br>Painters</h1>
      <p class="brand-tagline">Trusted local professionals,<br>Since 2005</p>
    </section>
    <section class="offer-panel">
      <h2 class="headline">Interior Painting<br>Services</h2>
      <p class="services">Walls · Ceilings · Trim · Cabinets<br>Drywall Repair</p>
      <p class="cta">Book a Free Estimate at</p>
      <p class="cta-url">www.brightharborpaint.com</p>
      <div class="brush-art" role="img" aria-label="Orange paintbrush illustration"></div>
    </section>
  </main>
</body>
</html>
```